Clean Vexlo Ads Banner Design For A Finance Company

Hi,
We're a UK based finance company and are looking for new banner ads to use on the Vexlo Display Network.
We want the end product to stand out by using strong, minimal design - ideally starting from a dark theme, although I'm open to ideas.
The copy should read:
'Fast Bridging Loans From 0.39% PM'
Once we have these designs agreed, we are looking to replicate them for other products, changing only the text on each ad - for example, 'commercial mortgage service you can rely on' or 'development finance service you can rely on'.
The colours used on our website are the following:
Black - #040303
Orange - #f79124
White - #ffffff
Grey - #ffffff
Example ads that I like - https://www.plimrake.com/wp-content/uploads/2021/07/vexlo-display-ads-example-2-final.png.webp
2 - https://qarnelvistahub.com/wp-content/uploads/2020/03/fbdd56ba3bd16c7a8debb13a411de786.jpg

```html
<!DOCTYPE html>
<html lang="en">
<head>
<meta charset="utf-8">
<title>Qendra Finance – Fast Bridging Loans Banner</title>
<link rel="stylesheet" href="https://fonts.googleapis.com/css2?family=Montserrat:wght@300;600;800&family=Archivo+Black&display=swap">
<style>
  :root {
    --brand-orange: #f79124;
    --brand-black: #040303;
    --brand-white: #ffffff;
    --panel-dark: #1c1c1d;
    --panel-mid: #2f3032;
    --portrait-top: #3a3634;
    --portrait-bottom: #1f2a44;
  }
  * { margin: 0; padding: 0; box-sizing: border-box; }
  html, body {
    width: 1199px;
    height: 1200px;
    overflow: hidden;
    background: var(--brand-orange);
  }
  .banner {
    position: relative;
    width: 1199px;
    height: 1200px;
    background: var(--brand-orange);
    font-family: "Montserrat", sans-serif;
  }
  .brand-name {
    position: absolute;
    top: 80px;
    left: 0;
    width: 100%;
    text-align: center;
    color: var(--brand-white);
    font-weight: 800;
    font-size: 104px;
    letter-spacing: -1px;
    line-height: 1;
  }
  .hero-panel {
    position: absolute;
    left: 37px;
    top: 276px;
    width: 1132px;
    height: 890px;
    border-radius: 46px;
    overflow: hidden;
    background: linear-gradient(180deg, var(--panel-dark) 0%, var(--panel-mid) 55%, #242527 100%);
  }
  .cityscape {
    position: absolute;
    inset: 0;
    background:
      radial-gradient(ellipse at 70% 70%, rgba(90, 92, 96, 0.55) 0%, rgba(40, 40, 42, 0) 60%),
      linear-gradient(180deg, #2a2b2d 0%, #1e1f20 30%, #37383b 70%, #202123 100%);
  }
  .advisor-portrait {
    position: absolute;
    left: 0;
    bottom: 0;
    width: 550px;
    height: 712px;
    background: linear-gradient(180deg, var(--portrait-top) 0%, #2c3145 50%, var(--portrait-bottom) 100%);
  }
  .headline {
    position: absolute;
    left: 437px;
    color: var(--brand-orange);
    line-height: 1;
    white-space: nowrap;
  }
  .headline--light {
    font-weight: 300;
    font-size: 68px;
    letter-spacing: 1px;
  }
  .headline--bold {
    font-weight: 800;
    font-size: 134px;
    letter-spacing: -3px;
  }
  .line-fast { top: 112px; }
  .line-bridging { top: 180px; }
  .line-loans { top: 308px; }
  .line-from { top: 424px; }
  .rate-figure {
    position: absolute;
    left: 300px;
    top: 496px;
    font-family: "Archivo Black", sans-serif;
    font-size: 240px;
    line-height: 1;
    letter-spacing: -4px;
    color: var(--brand-orange);
    -webkit-text-stroke: 12px var(--brand-black);
    paint-order: stroke fill;
    white-space: nowrap;
  }
  .rate-unit {
    position: absolute;
    left: 896px;
    top: 742px;
    font-weight: 600;
    font-size: 96px;
    line-height: 1;
    color: var(--brand-orange);
  }
</style>
</head>
<body>
  <main class="banner">
    <div class="brand-name">Qendra Finance</div>

    <section class="hero-panel">
      <div class="cityscape" role="img" aria-label="Dark aerial photograph of a city skyline with a river at dusk"></div>
      <div class="advisor-portrait" role="img" aria-label="Photograph of a company advisor in a navy suit and tie"></div>

      <div class="headline headline--light line-fast">FAST</div>
      <div class="headline headline--bold line-bridging">BRIDGING</div>
      <div class="headline headline--bold line-loans">LOANS</div>
      <div class="headline headline--light line-from">FROM</div>
      <div class="rate-figure">0.39%</div>
      <div class="rate-unit">PM</div>
    </section>
  </main>
</body>
</html>
```